Government Contracting business needs a website design.

Pellworth & Quine, LLC is a minority owned Service Disabled Veteran Owned Small Business (SDVOSB) that provides Strategic Planning, Public Health Emergency Response, and Data Management Solutions for Federal Civilian and Defense Agencies. We have over 20 years of experience helping health and defense agencies develop concept of operations, deploy assets and personnel in Hot Zones around the world, and deliver goods and services all of the globe.

We are a leader in the field of Data Management. We help our customers develop cloud migration and disaster recovery strategies. We are experts with database management, data replication, queries, consolidation, and records management.

We are looking for a very nice and simple website designs that states clearly what we do as a company and that is easy for our customers to follow. We would like to have some moving pictures that are base on our expertise. We want the website to be easy to use and have the scroll down features that keeps things all on the same page when clicking on the menu. I attached a document with what we need on the website. I will also attach our logo. We want it to look simple clean and very professional.

Target Market(s)

Government Contracting, Management Consulting, Health

Industry/Entity Type

Government

Coding

Coded - Design and coding required

Number of Pages Required

1 page

Font styles to use
Serif

Requirements
Must have
• Very nice picture slides that speaks to our capabilities in Disaster Response, Strategic Planning, and Database Management. Slick look and design. Make sure SDVOSB Logo is right at the beginning of website as our customers is looking for that certification. Very nice colors that blend well with our logo.
Nice to have
• Very nice and slick colors that blends well with logo.
Should not have
• Basic website design that are weary on the eye. No bright colors, just simple colors that looks good with logo.

```html
<!DOCTYPE html>
<html lang="en">
<head>
<meta charset="utf-8">
<title>Pellworth &amp; Quine, LLC</title>
<link rel="stylesheet" href="https://fonts.googleapis.com/css2?family=Open+Sans:wght@400;600;700&display=swap">
<style>
:root{
  --teal:#2b4859;
  --teal-dark:#223b4a;
  --nav:#d3d3d3;
  --ink:#333b40;
  --white:#ffffff;
  --footer:#262626;
  --footer-text:#a9a9a9;
  --graphic:#4a6482;
}
*{box-sizing:border-box;margin:0;padding:0}
html,body{width:1200px;height:2628px;overflow:hidden}
body{position:relative;background:var(--white);font-family:"Open Sans",Arial,sans-serif;color:var(--ink)}
a{color:inherit;text-decoration:none}
.abs{position:absolute}

/* header */
.site-header{left:0;top:0;width:1200px;height:121px;background:var(--teal)}
.brand{left:133px;top:36px;display:flex;align-items:center;gap:14px;color:var(--white);font-size:27px;font-weight:400}
.brand-mark{width:36px;height:36px;background:var(--white);border-radius:2px}
.cert-badge{left:986px;top:20px;width:80px;height:80px;border-radius:50%;background:var(--white);border:5px solid #d9dee3}
.main-nav{left:0;top:121px;width:1200px;height:47px;background:var(--nav)}
.nav-link{top:14px;font-size:15px;font-weight:600;color:#1f1f1f;text-transform:uppercase;white-space:nowrap}
.nav-link.is-active{color:var(--teal)}

/* hero */
.hero{left:0;top:168px;width:1200px;height:524px;
  background:linear-gradient(90deg,#12161b 0%,#1b2129 50%,#37414d 78%,#262c34 100%);
  clip-path:polygon(0 0,100% 0,100% 100%,832px 442px,0 100%)}
.hero-title{left:133px;top:304px;width:330px;font-size:17.5px;line-height:29px;font-weight:600;color:var(--white);text-transform:uppercase}
.btn-outline{display:flex;align-items:center;justify-content:center;border:1.5px solid var(--white);color:var(--white);font-size:13px;font-weight:600;text-transform:uppercase}
.hero-btn{left:133px;top:459px;width:113px;height:40px}
.hero-graphic{left:470px;top:300px;width:600px;height:190px;border-radius:4px;
  background:linear-gradient(90deg,rgba(111,139,173,.55) 0%,rgba(111,139,173,.4) 60%,rgba(255,255,255,.25) 100%)}
.slide-arrow{top:388px;width:24px;height:36px;background:#2c3138}

/* welcome */
.welcome-media{left:131px;top:766px;width:435px;height:254px;
  background:radial-gradient(circle at 40% 50%,#2f4a5e 0%,#15222e 60%,#0b1218 100%);
  clip-path:polygon(0 0,100% 0,87% 50%,100% 100%,0 100%)}
.section-title{font-size:23px;font-weight:600;color:var(--teal);text-transform:uppercase;letter-spacing:.3px}
.welcome-title{left:599px;top:759px;font-size:22.5px}
.welcome-text{left:599px;top:801px;width:466px;font-size:14px;line-height:23.6px;color:var(--ink)}
.btn-solid{display:flex;align-items:center;justify-content:center;background:var(--teal);color:var(--white);font-size:13px}
.welcome-btn{left:599px;top:983px;width:97px;height:38px}

/* capabilities */
.capabilities{left:0;top:1102px;width:1200px;height:515px;background:var(--teal);
  clip-path:polygon(0 0,100% 0,100% 388px,359px 515px,0 408px)}
.cap-title{left:0;top:1173px;width:1200px;text-align:center;color:var(--white)}
.cap-card{top:1230px;width:298px}
.cap-photo{height:175px}
.cap-label{background:var(--white);color:var(--teal);font-size:16px;font-weight:600;text-transform:uppercase;text-align:center;line-height:20px;padding-top:10px}
.cap-card.one .cap-label{height:85px;clip-path:polygon(0 0,100% 0,100% 66%,67% 100%,0 68%)}
.cap-card.two .cap-label{height:90px;clip-path:polygon(0 0,100% 0,100% 100%,45% 82%,0 100%)}
.cap-card.three .cap-label{height:85px;clip-path:polygon(0 0,100% 0,100% 52%,67% 100%,0 68%)}
.photo-planning{background:linear-gradient(180deg,#8a6a55 0%,#5b4a40 50%,#d9d9d9 80%,#2a2a2a 100%)}
.photo-response{background:linear-gradient(135deg,#d8cfc6 0%,#b02a32 50%,#7d1a20 100%)}
.photo-data{background:linear-gradient(90deg,#1b2a3b 0%,#2d4a68 50%,#101820 80%,#9a6a4a 100%)}

/* why hire */
.why-title{left:0;top:1693px;width:1200px;text-align:center}
.reason{display:flex;gap:14px;width:420px;font-size:15.5px;line-height:25px;color:var(--ink)}
.reason span{width:380px}
.tick{flex:none;width:26px;height:26px;margin-top:1px}

/* join */
.join{left:0;top:2011px;width:1200px;height:508px;background:var(--teal);
  clip-path:polygon(0 109px,359px 0,100% 100px,100% 100%,0 100%)}
.join-title{left:0;top:2127px;width:1200px;text-align:center;color:var(--white)}
.join-text{left:125px;top:2167px;width:950px;text-align:center;color:var(--white);font-size:16px;line-height:25.6px}
.join-btn{left:503px;top:2316px;width:194px;height:41px;font-size:13.5px}

/* footer */
.site-footer{left:0;top:2413px;width:1200px;height:215px;background:var(--footer);
  clip-path:polygon(0 106px,841px 0,100% 75px,100% 100%,0 100%)}
.footer-links{left:133px;top:2537px;font-size:12px;color:var(--footer-text);word-spacing:1px}
.footer-links span{margin:0 8px}
.copyright{left:133px;top:2568px;font-size:12px;color:var(--footer-text)}
.social{top:2549px;width:24px;height:24px;border-radius:50%}
</style>
</head>
<body>

<header class="site-header abs"></header>
<div class="brand abs"><span class="brand-mark"></span>Pellworth &amp; Quine</div>
<div class="cert-badge abs" role="img" aria-label="Veteran owned small business certification badge"></div>

<nav class="main-nav abs">
  <a class="nav-link abs is-active" style="left:133px">Home</a>
  <a class="nav-link abs" style="left:229px">About Us</a>
  <a class="nav-link abs" style="left:356px">Core Capabilities</a>
  <a class="nav-link abs" style="left:545px">Why Hire Us?</a>
  <a class="nav-link abs" style="left:699px">Our Partners</a>
  <a class="nav-link abs" style="left:862px">NAICS Codes</a>
  <a class="nav-link abs" style="left:1011px">Join Us</a>
</nav>

<section class="hero abs" role="img" aria-label="Businessman in a dark suit, slide about data consolidation"></section>
<div class="slide-arrow abs" style="left:0"></div>
<div class="slide-arrow abs" style="left:1176px"></div>
<h1 class="hero-title abs">We are a service disabled veteran owned small business (SDVOSB) specializing in mission oriented health IT for the defense and VA community.</h1>
<a class="btn-outline hero-btn abs">Read More</a>
<div class="hero-graphic abs" role="img" aria-label="Illustration of stacked documents being sorted into neat sheets"></div>

<section class="welcome-media abs" role="img" aria-label="Open hand holding glowing data hexagons"></section>
<h2 class="section-title welcome-title abs">Welcome to Pellworth &amp; Quine, LLC</h2>
<p class="welcome-text abs">Pellworth &amp; Quine, LLC is a minority owned Service Disabled Veteran Owned Small Business (SDVOSB) that provides Strategic Planning, Public Health Emergency Response, and Data ManagementSolutions for Federal Civilian and Defense Agencies.&nbsp; We have over 20 years of experience helping health and defense agencies develop concept of operations, deploy assets and personnel in Hot Zones around the world, and deliver goods and services all of the globe.</p>
<a class="btn-solid welcome-btn abs">Read More</a>

<section class="capabilities abs"></section>
<h2 class="section-title cap-title abs">Core Capabilities</h2>
<div class="cap-card one abs" style="left:131px">
  <div class="cap-photo photo-planning" role="img" aria-label="Businessman seated behind a giant outdoor chess set"></div>
  <div class="cap-label">Strategic Planning</div>
</div>
<div class="cap-card two abs" style="left:452px">
  <div class="cap-photo photo-response" role="img" aria-label="Emergency responder in red gear"></div>
  <div class="cap-label">Public Health<br>Emergency Response</div>
</div>
<div class="cap-card three abs" style="left:771px">
  <div class="cap-photo photo-data" role="img" aria-label="Server racks in a data center"></div>
  <div class="cap-label">Data Management<br>Services</div>
</div>

<h2 class="section-title why-title abs">Why Hire Us?</h2>
<div class="reason abs" style="left:134px;top:1750px">
  <svg class="tick" viewBox="0 0 26 26" aria-hidden="true"><circle cx="13" cy="13" r="13" fill="#3a3a3a"/><path d="M7 13.5l4 4 8-8" stroke="#fff" stroke-width="3" fill="none"/></svg>
  <span>Over 20 years of experience deploying assets and personnel to disaster zones around the US and the world.</span>
</div>
<div class="reason abs" style="left:649px;top:1750px">
  <svg class="tick" viewBox="0 0 26 26" aria-hidden="true"><circle cx="13" cy="13" r="13" fill="#3a3a3a"/><path d="M7 13.5l4 4 8-8" stroke="#fff" stroke-width="3" fill="none"/></svg>
  <span>Over 20 years of experience developing concept of operations and stakeholder management strategies for Federal Agencies.</span>
</div>
<div class="reason abs" style="left:134px;top:1854px">
  <svg class="tick" viewBox="0 0 26 26" aria-hidden="true"><circle cx="13" cy="13" r="13" fill="#3a3a3a"/><path d="M7 13.5l4 4 8-8" stroke="#fff" stroke-width="3" fill="none"/></svg>
  <span>Over 10 years of experience with database management and replications</span>
</div>
<div class="reason abs" style="left:649px;top:1854px">
  <svg class="tick" viewBox="0 0 26 26" aria-hidden="true"><circle cx="13" cy="13" r="13" fill="#3a3a3a"/><path d="M7 13.5l4 4 8-8" stroke="#fff" stroke-width="3" fill="none"/></svg>
  <span>Highly educated consultants with over 90% possessing advance degrees and industry certifications</span>
</div>

<section class="join abs"></section>
<h2 class="section-title join-title abs">Join Us</h2>
<p class="join-text abs">Pellworth &amp; Quine strives to provide an outstanding work environment for our employees. We invest in our people and believe strongly in creating an environment where our employees are free to work on innovative solutions that meet our clients' needs.&nbsp; We promote true work-life balance, career advancement, health, and financial security and fun in the work place.&nbsp; We encourage our employees to participate in our internal operation and help to develop them into the ideal consultants that our clients seek.</p>
<a class="btn-outline join-btn abs">View Our Job Openings</a>

<footer class="site-footer abs"></footer>
<div class="footer-links abs">Home<span>|</span>About Us<span>|</span>Core Capabilities<span>|</span>Why Hire Us?<span>|</span>Our Partners<span>|</span>NAICS Codes<span>|</span>Join Us</div>
<div class="copyright abs">Copyright &copy; 2018&nbsp; PELLWORTH &amp; QUINE, LLC.&nbsp; All rights reserved.</div>
<span class="social abs" style="left:945px;background:#2f4f8f"></span>
<span class="social abs" style="left:977px;background:#2b8fd6"></span>
<span class="social abs" style="left:1010px;background:#1f6ea8"></span>
<span class="social abs" style="left:1043px;background:#d93a2f"></span>

</body>
</html>
```